Verodex business card

Business card for sustainable investment company called "Verodex". Verodex is an exchange platform selling carbon credits between buyers and sellers. Carbon Credits are an environmental commodity for reducing global carbon emissions.

the card should obviously have our logo and the theme should be sustainability/environment mixed with a trading platform.

Contact Information for Business Card

Logo, Name, Title, Phone, Email

Colors
0054AA
0677BA
7BADD7
CADEEF
E8F1F8
0094D4
00A9DD
6FCCEA
C7EBF8
E9F6FB
00AB8E
00BBA5
67D7C9
C6EFE9
E9F9F6
59FF00
82FF00
B8FF75
E3FFCB
F4FFEA

```html
<!DOCTYPE html>
<html lang="en">
<head>
<meta charset="utf-8">
<title>Verodex Business Card</title>
<link href="https://fonts.googleapis.com/css2?family=Montserrat:wght@700;800&family=Arimo:ital,wght@0,400;1,400&display=swap" rel="stylesheet">
<style>
  :root {
    --backdrop: #0c0d10;
    --card-navy: #1a2844;
    --card-navy-deep: #15213a;
    --white: #f4f6fa;
    --muted: #dfe6f1;
    --cyan: #2fd6ea;
    --blue: #1d63e0;
    --icon-blue: #2b8fe8;
    --divider: #c9d3e3;
  }
  * { margin: 0; padding: 0; box-sizing: border-box; }
  html, body { width: 1200px; height: 963px; overflow: hidden; }
  body {
    background: var(--backdrop);
    display: flex;
    flex-direction: column;
    align-items: center;
    justify-content: center;
    gap: 70px;
  }
  .card {
    position: relative;
    width: 540px;
    height: 309px;
    border-radius: 22px;
    background: linear-gradient(160deg, var(--card-navy-deep), var(--card-navy));
    overflow: hidden;
    border-right: 3px solid var(--blue);
  }
  .card::after {
    content: "";
    position: absolute;
    left: 0; right: 0; bottom: 0;
    height: 3px;
    background: linear-gradient(90deg, var(--cyan), var(--blue));
  }
  /* Front */
  .brand {
    position: absolute;
    top: 62px;
    left: 0; right: 0;
    display: flex;
    justify-content: center;
    align-items: center;
    gap: 12px;
  }
  .brand-mark {
    width: 16px; height: 16px;
    background: var(--cyan);
  }
  .brand-name {
    font-family: "Montserrat", sans-serif;
    font-weight: 800;
    font-size: 40px;
    letter-spacing: 2px;
    color: var(--white);
  }
  .details {
    position: absolute;
    top: 160px;
    left: 0; right: 0;
    display: flex;
    justify-content: center;
    align-items: stretch;
    gap: 22px;
  }
  .person { text-align: right; padding-top: 8px; }
  .person-name {
    font-family: "Montserrat", sans-serif;
    font-weight: 800;
    font-size: 17px;
    letter-spacing: 0.5px;
    background: linear-gradient(90deg, var(--blue), var(--cyan));
    -webkit-background-clip: text;
    background-clip: text;
    color: transparent;
  }
  .person-title {
    font-family: "Arimo", sans-serif;
    font-style: italic;
    font-size: 14px;
    color: var(--muted);
    margin-top: 2px;
  }
  .divider { width: 1px; background: var(--divider); }
  .contacts { list-style: none; }
  .contacts li {
    display: flex;
    align-items: center;
    gap: 8px;
    font-family: "Arimo", sans-serif;
    font-style: italic;
    font-size: 14px;
    color: var(--white);
    line-height: 22px;
  }
  .contacts svg { width: 13px; height: 13px; flex: none; }
  .address {
    position: absolute;
    bottom: 38px;
    left: 0; right: 0;
    text-align: center;
    font-family: "Arimo", sans-serif;
    font-style: italic;
    font-size: 14px;
    color: var(--muted);
  }
  /* Back */
  .card-back .back-name {
    position: absolute;
    right: 38px;
    bottom: 34px;
    font-family: "Montserrat", sans-serif;
    font-weight: 800;
    font-size: 44px;
    letter-spacing: 2px;
    color: var(--white);
  }
</style>
</head>
<body>
  <section class="card card-front">
    <div class="brand">
      <span class="brand-mark"></span>
      <span class="brand-name">VERODEX</span>
    </div>
    <div class="details">
      <div class="person">
        <p class="person-name">MARCUS HALE</p>
        <p class="person-title">Manager</p>
      </div>
      <span class="divider"></span>
      <ul class="contacts">
        <li>
          <svg viewBox="0 0 16 16" aria-hidden="true"><path d="M4 1.5l2.5 3-1.4 1.6a8 8 0 0 0 4.8 4.8l1.6-1.4 3 2.5-1.8 2.3C7 14 2 9 1.7 3.3z" fill="var(--icon-blue)"/></svg>
          415-555-0172
        </li>
        <li>
          <svg viewBox="0 0 16 16" aria-hidden="true"><rect x="1.5" y="3.5" width="13" height="9" fill="none" stroke="var(--icon-blue)" stroke-width="1.3"/><path d="M1.5 3.5L8 9l6.5-5.5" fill="none" stroke="var(--icon-blue)" stroke-width="1.3"/></svg>
          mhale@verodex.com
        </li>
        <li>
          <svg viewBox="0 0 16 16" aria-hidden="true"><circle cx="8" cy="8" r="6.5" fill="none" stroke="var(--icon-blue)" stroke-width="1.3"/><ellipse cx="8" cy="8" rx="2.8" ry="6.5" fill="none" stroke="var(--icon-blue)" stroke-width="1.1"/><path d="M1.5 8h13M2.5 4.8h11M2.5 11.2h11" stroke="var(--icon-blue)" stroke-width="1"/></svg>
          www.verodex.com
        </li>
      </ul>
    </div>
    <p class="address">48 Harbor Lane, Portland, OR 97204</p>
  </section>

  <section class="card card-back">
    <span class="back-name">VERODEX</span>
  </section>
</body>
</html>
```